Präsentationsvorlagen für Unternehmensberatung im Finanzbereich
Zielgruppe
Unternehmensberatung für den Finanzbereich, Compliance Beratung/Implementierung regulatorischer Projekte, Bereitstellung von Management Resourcen, Trainings/Coaching/Seminare. Zielgruppe: Banken, Fonds und Investmentgesellschaften
Aufgabenstellung
hochwertiges design, clean, keine standard bilder von Bergen, Tastaturen oder Menschen, die sich unterhalten. eher Architektur Bilder, Bilder sollen Bezug zum Inhalt haben, Verlässlichkeit, Professionalität, Kundenfokus ausstrahlen. 4 Services sollen präsentiert werden, ggf mit Bildlogo in unterschiedlichen Farben verbinden.

```html
<!DOCTYPE html>
<html lang="de">
<head>
<meta charset="utf-8">
<title>Weissenau Sàrl – Compliance Beratung</title>
<link rel="stylesheet" href="https://fonts.googleapis.com/css2?family=IBM+Plex+Mono:wght@300;400&family=Inter:wght@200&display=swap">
<style>
  :root {
    --concrete-dark: #6f706d;
    --concrete-mid: #8d8e8a;
    --sky: #e6e8e5;
    --sky-tint: #dfeceb;
    --panel: #f5f5f5;
    --rule: #1c1c1c;
    --ink: #222222;
    --brand: #4a5261;
    --ghost-number: rgba(0, 0, 0, 0.05);
  }
  * { margin: 0; padding: 0; box-sizing: border-box; }
  html, body { width: 1200px; height: 675px; overflow: hidden; background: var(--panel); }
  .slide {
    position: relative;
    width: 1200px;
    height: 675px;
    overflow: hidden;
    background: var(--panel);
    font-family: "IBM Plex Mono", monospace;
  }
  .cover-photo {
    position: absolute;
    left: 0; top: 0;
    width: 697px; height: 675px;
    background:
      linear-gradient(128deg, var(--concrete-dark) 0%, var(--concrete-mid) 38%, transparent 38.2%),
      linear-gradient(180deg, var(--sky) 0%, var(--sky) 70%, var(--sky-tint) 100%);
  }
  .panel-right {
    position: absolute;
    left: 697px; top: 0;
    width: 503px; height: 675px;
    background: var(--panel);
  }
  .top-rule {
    position: absolute;
    left: 0; top: 67px;
    width: 1055px; height: 1px;
    background: var(--rule);
  }
  .ghost-number {
    position: absolute;
    left: 760px; top: 262px;
    font-family: "Inter", sans-serif;
    font-weight: 200;
    font-size: 316px;
    line-height: 1;
    letter-spacing: -6px;
    color: var(--ghost-number);
  }
  .side-label, .page-number {
    position: absolute;
    writing-mode: vertical-rl;
    font-weight: 300;
    color: var(--ink);
  }
  .side-label { left: 1105px; top: 67px; font-size: 17px; letter-spacing: 0.5px; }
  .page-number { left: 1107px; top: 583px; font-size: 14px; font-weight: 400; }
  .brand-name {
    position: absolute;
    left: 444px; top: 452px;
    width: 504px;
    text-align: center;
    font-weight: 400;
    font-size: 38px;
    letter-spacing: 6px;
    line-height: 1.25;
    color: var(--brand);
  }
</style>
</head>
<body>
<main class="slide">
  <div class="cover-photo" role="img" aria-label="Architekturfoto: Blick an einer Betonfassade mit Fensterbändern in den hellen Himmel"></div>
  <div class="panel-right"></div>
  <div class="top-rule"></div>
  <div class="ghost-number" aria-hidden="true">01</div>
  <div class="brand-name">WEISSENAU<br>SÀRL</div>
  <div class="side-label">Compliance Beratung</div>
  <div class="page-number">01</div>
</main>
</body>
</html>
```